Flu Vaccination Poster

I would like a banner designed to display from the ceiling in my pharmacy promoting flu vaccination.
In large words, it should say "Flu Vaccination"
In smaller text it should say "Available here. See in store for details"
It should also display our website kestrelvalepharmacy.com.au and have a message for more information visit the website.
Currently patients required to pay for the service, however in May this year the vaccine will become free for everyone, so I would like to put a sticker on the sign in May saying "FREE" and then remove the sticker when no longer free. The banner dimensions are "2.19m wide x 0.61m tall.
I have uploaded logo files plus a photo of a previously used banner which is no longer relevant. More formats of logo files are available if required.

```html
<!DOCTYPE html>
<html lang="en">
<head>
<meta charset="utf-8">
<title>Flu Vaccination Banner – Kestrel Vale Pharmacy</title>
<link rel="stylesheet" href="https://fonts.googleapis.com/css2?family=Montserrat:wght@500;900&family=Inter:wght@400;800&family=Anton&display=swap">
<style>
  :root {
    --navy: #233d66;
    --royal: #1c5aa3;
    --sky: #a9d6ee;
    --magenta: #d81b60;
    --white: #ffffff;
    --backdrop: #c4c4c4;
  }
  * { margin: 0; padding: 0; box-sizing: border-box; }
  html, body { width: 1200px; height: 754px; overflow: hidden; }
  body { background: var(--backdrop); position: relative; }

  .banner {
    position: absolute;
    left: 99px;
    width: 1001px;
    height: 280px;
    background: var(--white);
  }
  .banner--with-brand { top: 63px; }
  .banner--plain { top: 398px; }

  .headline {
    position: absolute;
    top: 42px;
    left: 0;
    width: 100%;
    text-align: center;
    font-family: "Montserrat", sans-serif;
    font-size: 100px;
    line-height: 1;
    color: var(--navy);
    white-space: nowrap;
    letter-spacing: -0.01em;
  }
  .headline__strong { font-weight: 900; letter-spacing: -0.03em; }
  .headline__light { font-weight: 500; }

  .tagline {
    position: absolute;
    top: 137px;
    left: 0;
    width: 100%;
    text-align: center;
    font-family: "Inter", sans-serif;
    font-size: 44px;
    font-weight: 400;
    letter-spacing: -0.035em;
    color: var(--royal);
    white-space: nowrap;
  }
  .tagline strong { font-weight: 800; letter-spacing: -0.045em; }

  .info-band {
    position: absolute;
    left: 0;
    bottom: 0;
    width: 100%;
    height: 72px;
    background: var(--navy);
  }
  .brand-name {
    position: absolute;
    left: 24px;
    top: 18px;
    width: 120px;
    font-family: "Inter", sans-serif;
    font-weight: 800;
    font-size: 15px;
    line-height: 17px;
    letter-spacing: -0.02em;
    color: var(--white);
  }
  .contact-line {
    position: absolute;
    left: 0;
    width: 100%;
    top: 21px;
    padding-left: 192px;
    font-family: "Inter", sans-serif;
    font-weight: 800;
    font-size: 25px;
    letter-spacing: -0.035em;
    color: var(--sky);
    white-space: nowrap;
  }
  .contact-line__dot { color: var(--magenta); margin: 0 10px; font-size: 18px; vertical-align: 3px; }

  .free-sticker {
    position: absolute;
    width: 88px;
    height: 88px;
    border-radius: 50%;
    background: var(--magenta);
    display: flex;
    align-items: center;
    justify-content: center;
    font-family: "Anton", sans-serif;
    font-size: 40px;
    color: var(--white);
    letter-spacing: 0.01em;
  }
  .free-sticker--right { left: 884px; top: 164px; }
  .free-sticker--right span { transform: rotate(-8deg); }
  .free-sticker--left { left: 36px; top: 164px; }
</style>
</head>
<body>

  <section class="banner banner--with-brand">
    <h1 class="headline"><span class="headline__strong">FLU</span> <span class="headline__light">VACCINATION</span></h1>
    <p class="tagline">Available here. <strong>See in store</strong> for details</p>
    <div class="info-band">
      <div class="brand-name">Kestrel Vale Pharmacy</div>
      <p class="contact-line">For More Details<span class="contact-line__dot">•</span>www.kestrelvalepharmacy.com.au</p>
    </div>
    <div class="free-sticker free-sticker--right"><span>FREE</span></div>
  </section>

  <section class="banner banner--plain">
    <h1 class="headline"><span class="headline__strong">FLU</span> <span class="headline__light">VACCINATION</span></h1>
    <p class="tagline">Available here. <strong>See in store</strong> for details</p>
    <div class="info-band">
      <p class="contact-line">For More Details<span class="contact-line__dot">•</span>www.kestrelvalepharmacy.com.au</p>
    </div>
    <div class="free-sticker free-sticker--left"><span>FREE</span></div>
  </section>

</body>
</html>
```